Brochure Design Project

We sell and install rollout shelves for existing kitchen and bathroom cabinets. These rollout shelves are made of wood with dovetail joints. We also organize cabinets with pullouts, lazy susans, trash can pullouts, drawer organizers, and offer a selection of cabinet handles and knobs that we can also install.

Need extra days to review

```html
<!DOCTYPE html>
<html lang="en">
<head>
<meta charset="utf-8">
<title>Rollout Shelves Trifold Brochure – Outside Spreads</title>
<link rel="stylesheet" href="https://fonts.googleapis.com/css2?family=Montserrat:wght@400;600;700;800&family=Open+Sans:wght@400;600&display=swap">
<style>
  :root{
    --stage:#3f3f3f;
    --paper:#ffffff;
    --paper-soft:#f5f6f5;
    --green:#68c32a;
    --green-deep:#4fa81c;
    --ink:#2e2e2e;
    --ink-soft:#555555;
    --rule:#d8d8d8;
    --label:#f2f2f2;
  }
  *{box-sizing:border-box;margin:0;padding:0}
  html,body{width:781px;height:1200px;overflow:hidden;background:var(--stage)}
  body{position:relative;font-family:"Open Sans",Arial,sans-serif;color:var(--ink)}

  .spread{position:absolute;left:56px;width:672px;height:522px;background:var(--paper);overflow:hidden}
  .spread--one{top:44px}
  .spread--two{top:620px}
  .spread-art{position:absolute;inset:0;width:672px;height:522px}

  .spread-label{position:absolute;left:0;width:781px;text-align:center;
    font-family:"Open Sans",Arial,sans-serif;font-size:20px;color:var(--label);letter-spacing:.2px}
  .spread-label--one{top:576px}
  .spread-label--two{top:1154px}

  /* left panel */
  .about{position:absolute;left:0;top:0;width:222px}
  .about-title{position:absolute;top:38px;width:222px;text-align:center;
    font-family:"Montserrat",sans-serif;font-size:13px;font-weight:600;color:var(--ink)}
  .about-title span{color:var(--green);font-weight:400}
  .about-intro{position:absolute;left:20px;top:64px;width:186px;font-size:7.4px;line-height:1.35;color:var(--ink)}
  .quote-box{position:absolute;left:19px;top:132px;width:184px;height:153px;
    border:1px dashed var(--green);border-radius:7px;padding:19px 9px 0 9px;background:var(--paper)}
  .quote-box p{font-size:7.4px;line-height:1.33;text-align:justify;color:var(--ink);margin-bottom:6px}
  .quote-mark{position:absolute;height:24px;overflow:hidden;font-family:"Montserrat",sans-serif;font-weight:800;
    font-size:42px;color:#c9c9c9;line-height:1;background:var(--paper);padding:0 3px}
  .quote-mark--open{left:10px;top:-12px}
  .quote-mark--close{right:10px;bottom:-12px}

  /* brand mark */
  .brand{position:absolute;text-align:center;width:150px}
  .brand-name{font-family:"Montserrat",sans-serif;font-weight:800;font-size:19px;color:var(--green);
    letter-spacing:.5px;line-height:1}
  .brand-sub{font-family:"Montserrat",sans-serif;font-weight:800;font-size:6.4px;color:var(--green);
    letter-spacing:2.2px;margin-top:3px;border-top:1px solid var(--green);padding-top:2px;display:inline-block}

  /* middle panel */
  .contact{position:absolute;left:222px;top:0;width:224px;height:522px}
  .contact .brand{left:37px;top:330px}
  .contact-title{position:absolute;top:373px;width:224px;text-align:center;
    font-family:"Montserrat",sans-serif;font-weight:700;font-size:13px;color:var(--ink)}
  .contact-title span{color:var(--green)}
  .contact-blurb{position:absolute;top:395px;left:22px;width:180px;text-align:center;
    font-size:6.6px;line-height:1.4;color:var(--ink-soft)}
  .contact-icons{position:absolute;top:424px;left:0;width:224px;display:flex;justify-content:center;gap:8px}
  .contact-icons svg{width:21px;height:21px}
  .contact-lines{position:absolute;top:452px;width:224px;text-align:center;font-size:8.4px;line-height:12px;color:var(--ink)}
  .contact-phone{font-family:"Montserrat",sans-serif;font-weight:700;font-size:10.5px;color:var(--green)}

  /* right panel */
  .cover{position:absolute;left:446px;top:0;width:226px;height:522px}
  .cover .brand{left:38px;top:333px}
  .cover-lead{position:absolute;top:379px;width:226px;text-align:center;font-size:9.6px;line-height:14px;color:var(--ink)}
  .cover-box{position:absolute;left:35px;top:386px;width:157px;height:88px;
    border:1px solid var(--green);border-top:none}
  .cover-box::before,.cover-box::after{content:"";position:absolute;top:0;width:16px;border-top:1px solid var(--green)}
  .cover-box::before{left:0}.cover-box::after{right:0}
  .cover-headline{position:absolute;top:8px;width:100%;text-align:center;
    font-family:"Montserrat",sans-serif;font-weight:800;font-size:27px;line-height:25px;color:var(--green);letter-spacing:.4px}
  .cover-sub{position:absolute;top:58px;width:100%;text-align:center;font-size:9.6px;line-height:12.5px;color:var(--ink)}
  .cover-web{position:absolute;top:501px;left:40px;width:186px;text-align:center;
    font-size:8.4px;letter-spacing:2px;color:var(--paper)}
</style>
</head>
<body>

<!-- ============ Spread one ============ -->
<section class="spread spread--one">
  <svg class="spread-art" viewBox="0 0 672 522">
    <defs>
      <linearGradient id="wood1" x1="0" y1="0" x2="1" y2="1">
        <stop offset="0" stop-color="#b9844a"/><stop offset="1" stop-color="#7d5128"/>
      </linearGradient>
      <linearGradient id="white1" x1="0" y1="0" x2="0" y2="1">
        <stop offset="0" stop-color="#eef0f2"/><stop offset="1" stop-color="#cfd4d8"/>
      </linearGradient>
      <linearGradient id="vanity1" x1="0" y1="0" x2="0" y2="1">
        <stop offset="0" stop-color="#d9d4cc"/><stop offset="1" stop-color="#b07a45"/>
      </linearGradient>
    </defs>
    <rect x="222" y="0" width="450" height="522" fill="var(--paper-soft)"/>
    <line x1="446" y1="300" x2="446" y2="522" stroke="#ececec"/>
    <path d="M0,0 H222 C150,10 70,14 0,34 Z" fill="var(--green)"/>
    <path d="M0,34 C70,14 150,10 222,0 C150,16 70,22 0,44 Z" fill="#e4e4e4"/>
    <path role="img" aria-label="Photo of wooden kitchen cabinet with an open rollout shelf holding pots and a toaster" d="M222,0 H672 V232 C620,282 520,318 440,306 C360,294 280,252 222,232 Z" fill="url(#wood1)"/>
    <path d="M222,240 C280,262 360,304 440,314 C520,326 620,290 672,240" fill="none" stroke="var(--green)" stroke-width="6"/>
    <path d="M222,250 C290,274 360,314 440,322 C520,332 620,300 672,252" fill="none" stroke="#d6d6d6" stroke-width="1.2"/>
    <circle cx="336" cy="240" r="79" fill="#f1f1f1" stroke="#dedede"/>
    <circle role="img" aria-label="Photo of a wooden bathroom vanity with twin sinks and mirror" cx="336" cy="240" r="69" fill="url(#vanity1)"/>
    <path d="M0,334 C70,292 160,290 222,318" fill="none" stroke="var(--green)" stroke-width="7"/>
    <path role="img" aria-label="Photo of a white kitchen counter with knives, vegetables and fruit" d="M0,346 C70,304 160,302 222,330 V522 H0 Z" fill="url(#white1)"/>
    <path d="M340,522 C450,500 570,492 672,484" fill="none" stroke="#d6d6d6" stroke-width="1.2"/>
    <path d="M360,522 C460,506 580,496 672,490 V522 Z" fill="var(--green)"/>
  </svg>

  <div class="about">
    <h2 class="about-title"><span>WHO</span> WE ARE</h2>
    <p class="about-intro">Lorem Ipsum is simply dummy text of the printing and typesetting industry. Lorem Ipsum has been the industry's standard dummy text ever since the 1500s,</p>
    <div class="quote-box">
      <span class="quote-mark quote-mark--open">“</span>
      <p>Lorem Ipsum is simply dummy text of the printing and typesetting industry. Lorem Ipsum has been the industry's standard dummy text ever since the 1500s, when an unknown printer took a galley of type and scrambled it to make a type specimen book.</p>
      <p>Lorem Ipsum is simply dummy text of the printing and typesetting industry. Lorem Ipsum has been the industry's standard dummy text ever since the 1500s,</p>
      <span class="quote-mark quote-mark--close">”</span>
    </div>
  </div>

  <div class="contact">
    <div class="brand"><div class="brand-name">ROLLWELL</div><div class="brand-sub">CABINETRY</div></div>
    <h3 class="contact-title">GET <span>IN TOUCH</span></h3>
    <p class="contact-blurb">Lorem Ipsum is simply dummy text of the printing and typesetting industry.</p>
    <div class="contact-icons">
      <svg viewBox="0 0 20 20"><circle cx="10" cy="10" r="10" fill="var(--green)"/><path d="M10,4.5a3.3,3.3 0 0 0-3.3,3.3c0,2.6 3.3,6.7 3.3,6.7s3.3-4.1 3.3-6.7A3.3,3.3 0 0 0 10,4.5z" fill="#fff"/><circle cx="10" cy="7.9" r="1.2" fill="var(--green)"/></svg>
      <svg viewBox="0 0 20 20"><circle cx="10" cy="10" r="10" fill="var(--green)"/><rect x="7" y="4.5" width="6" height="11" rx="1.2" fill="none" stroke="#fff" stroke-width="1.3"/><circle cx="10" cy="13.3" r=".7" fill="#fff"/></svg>
      <svg viewBox="0 0 20 20"><circle cx="10" cy="10" r="10" fill="var(--green)"/><g fill="none" stroke="#fff" stroke-width="1"><circle cx="10" cy="10" r="5"/><ellipse cx="10" cy="10" rx="2.2" ry="5"/><line x1="5" y1="10" x2="15" y2="10"/></g></svg>
    </div>
    <div class="contact-lines">
      Your Address Goes Here<br>
      <span class="contact-phone">0123-456-789</span><br>
      info@yourmailid.com<br>
      www.yourwebsite.com
    </div>
  </div>

  <div class="cover">
    <div class="brand"><div class="brand-name">ROLLWELL</div><div class="brand-sub">CABINETRY</div></div>
    <p class="cover-lead">We sell and install</p>
    <div class="cover-box">
      <h1 class="cover-headline">ROLLOUT<br>SHELVES</h1>
      <p class="cover-sub">For Existing Kitchen And<br>Bathroom Cabinets</p>
    </div>
    <p class="cover-web">www.yourwebsite.com</p>
  </div>
</section>
<p class="spread-label spread-label--one">Brochure_outside1</p>

<!-- ============ Spread two ============ -->
<section class="spread spread--two">
  <svg class="spread-art" viewBox="0 0 672 522">
    <defs>
      <linearGradient id="wood2" x1="0" y1="0" x2="1" y2="1">
        <stop offset="0" stop-color="#b9844a"/><stop offset="1" stop-color="#7d5128"/>
      </linearGradient>
      <linearGradient id="white2" x1="0" y1="0" x2="0" y2="1">
        <stop offset="0" stop-color="#eef0f2"/><stop offset="1" stop-color="#cfd4d8"/>
      </linearGradient>
      <linearGradient id="vanity2" x1="0" y1="0" x2="0" y2="1">
        <stop offset="0" stop-color="#d9d4cc"/><stop offset="1" stop-color="#b07a45"/>
      </linearGradient>
    </defs>
    <rect x="222" y="0" width="450" height="522" fill="var(--paper-soft)"/>
    <line x1="446" y1="300" x2="446" y2="522" stroke="#ececec"/>
    <path d="M0,0 H222 C150,10 70,14 0,34 Z" fill="var(--green)"/>
    <path d="M0,34 C70,14 150,10 222,0 C150,16 70,22 0,44 Z" fill="#e4e4e4"/>
    <path role="img" aria-label="Photo of a white kitchen with knives, vegetables, fruit and a sink" d="M222,0 H672 V232 C620,282 520,318 440,306 C360,294 280,252 222,232 Z" fill="url(#white2)"/>
    <path d="M222,240 C280,262 360,304 440,314 C520,326 620,290 672,240" fill="none" stroke="var(--green)" stroke-width="6"/>
    <path d="M222,250 C290,274 360,314 440,322 C520,332 620,300 672,252" fill="none" stroke="#d6d6d6" stroke-width="1.2"/>
    <circle cx="336" cy="240" r="79" fill="#f1f1f1" stroke="#dedede"/>
    <circle role="img" aria-label="Photo of a wooden bathroom vanity with twin sinks and mirror" cx="336" cy="240" r="69" fill="url(#vanity2)"/>
    <path d="M0,334 C70,292 160,290 222,318" fill="none" stroke="var(--green)" stroke-width="7"/>
    <path role="img" aria-label="Photo of wooden cabinets with an open rollout shelf holding pots" d="M0,346 C70,304 160,302 222,330 V522 H0 Z" fill="url(#wood2)"/>
    <path d="M340,522 C450,500 570,492 672,484" fill="none" stroke="#d6d6d6" stroke-width="1.2"/>
    <path d="M360,522 C460,506 580,496 672,490 V522 Z" fill="var(--green)"/>
  </svg>

  <div class="about">
    <h2 class="about-title"><span>WHO</span> WE ARE</h2>
    <p class="about-intro">Lorem Ipsum is simply dummy text of the printing and typesetting industry. Lorem Ipsum has been the industry's standard dummy text ever since the 1500s,</p>
    <div class="quote-box">
      <span class="quote-mark quote-mark--open">“</span>
      <p>Lorem Ipsum is simply dummy text of the printing and typesetting industry. Lorem Ipsum has been the industry's standard dummy text ever since the 1500s, when an unknown printer took a galley of type and scrambled it to make a type specimen book.</p>
      <p>Lorem Ipsum is simply dummy text of the printing and typesetting industry. Lorem Ipsum has been the industry's standard dummy text ever since the 1500s,</p>
      <span class="quote-mark quote-mark--close">”</span>
    </div>
  </div>

  <div class="contact">
    <div class="brand"><div class="brand-name">ROLLWELL</div><div class="brand-sub">CABINETRY</div></div>
    <h3 class="contact-title">GET <span>IN TOUCH</span></h3>
    <p class="contact-blurb">Lorem Ipsum is simply dummy text of the printing and typesetting industry.</p>
    <div class="contact-icons">
      <svg viewBox="0 0 20 20"><circle cx="10" cy="10" r="10" fill="var(--green)"/><path d="M10,4.5a3.3,3.3 0 0 0-3.3,3.3c0,2.6 3.3,6.7 3.3,6.7s3.3-4.1 3.3-6.7A3.3,3.3 0 0 0 10,4.5z" fill="#fff"/><circle cx="10" cy="7.9" r="1.2" fill="var(--green)"/></svg>
      <svg viewBox="0 0 20 20"><circle cx="10" cy="10" r="10" fill="var(--green)"/><rect x="7" y="4.5" width="6" height="11" rx="1.2" fill="none" stroke="#fff" stroke-width="1.3"/><circle cx="10" cy="13.3" r=".7" fill="#fff"/></svg>
      <svg viewBox="0 0 20 20"><circle cx="10" cy="10" r="10" fill="var(--green)"/><g fill="none" stroke="#fff" stroke-width="1"><circle cx="10" cy="10" r="5"/><ellipse cx="10" cy="10" rx="2.2" ry="5"/><line x1="5" y1="10" x2="15" y2="10"/></g></svg>
    </div>
    <div class="contact-lines">
      Your Address Goes Here<br>
      <span class="contact-phone">0123-456-789</span><br>
      info@yourmailid.com<br>
      www.yourwebsite.com
    </div>
  </div>

  <div class="cover">
    <div class="brand"><div class="brand-name">ROLLWELL</div><div class="brand-sub">CABINETRY</div></div>
    <p class="cover-lead">We sell and install</p>
    <div class="cover-box">
      <h1 class="cover-headline">ROLLOUT<br>SHELVES</h1>
      <p class="cover-sub">For Existing Kitchen And<br>Bathroom Cabinets</p>
    </div>
    <p class="cover-web">www.yourwebsite.com</p>
  </div>
</section>
<p class="spread-label spread-label--two">Brochure_outside2</p>

</body>
</html>
```